A website for a Maltese Law Firm

Our law firm needs a website to further its business. The site should have a simple yet effective design. We would need the following sections: About us, Practice Areas, About Malta, Contact. These should be further split as follows:

About us: Our firm, Our values, What others say, Offices

Practice Areas: Crimimal, Citizenship & Residence, Sovereign Patron Pathway, Criminal Defence, Civil Litigation, Arbitration and ADR, Commercial and Corporate, Media Law.

About Malta: just one section.

Contact: Just one section

We would also need a news feed at the front of the site to include latest news regarding our cases.

At the bottom we need a section for our Terms and a Privacy Statement.

Our logo is being attached.

Target Market(s)

All clients looking for legal assistance in Malta

Industry/Entity Type

Legal

Coding

Coded - Design and coding required

Number of Pages Required

1 page

Requirements
Must have
• It must be simple yet striking.

```html
<!DOCTYPE html>
<html lang="en">
<head>
<meta charset="utf-8">
<title>Calleja &amp; Ferro Advocates</title>
<link href="https://fonts.googleapis.com/css2?family=Cinzel:wght@400;600;700&family=Lato:ital,wght@0,400;0,700;1,400&display=swap" rel="stylesheet">
<style>
:root{
  --ink:#2b2d33;
  --dark:#2d2f35;
  --paper:#ffffff;
  --mist:#ebebeb;
  --steel:#a9aaac;
  --button:#b5b6b8;
  --line:#cfcfcf;
  --text:#333333;
  --muted:#555555;
}
*{box-sizing:border-box;margin:0;padding:0}
html,body{width:1200px;height:2723px;overflow:hidden}
body{font-family:"Lato",Arial,sans-serif;color:var(--text);background:var(--paper);position:relative}
section,header,nav,footer{position:absolute;left:0;width:1200px}
.abs{position:absolute}
h2.section-title{font-family:"Cinzel",Georgia,serif;font-weight:400;font-size:29px;color:var(--ink);text-align:center;position:absolute;left:0;width:1200px}

/* header */
.site-header{top:0;height:105px;background:var(--paper)}
.brand{left:69px;top:28px;font-family:"Cinzel",Georgia,serif;font-size:36px;font-weight:600;color:var(--ink);letter-spacing:1px;white-space:nowrap}
.contact-line{left:898px;font-weight:700;font-size:16px;color:var(--ink);display:flex;align-items:center;gap:12px;white-space:nowrap}
.contact-line svg{width:26px;height:26px}

/* nav */
.main-nav{top:105px;height:48px;background:var(--dark)}
.main-nav ul{list-style:none;display:flex;position:absolute;left:69px;top:0;height:48px}
.main-nav li{height:48px;display:flex;align-items:center;justify-content:center;font-family:"Cinzel",Georgia,serif;font-size:15px;color:#fff;border-right:1px solid #55575d;white-space:nowrap}
.main-nav li.active{background:var(--button);color:var(--ink)}

/* hero */
.hero{top:153px;height:424px;overflow:hidden}
.hero-photo{position:absolute;inset:0;background:linear-gradient(180deg,#b9a58a 0%,#c08f5c 40%,#9c6a3e 75%,#6e4a2c 100%)}
.hero-title{top:260px;left:0;width:1200px;text-align:center;font-family:"Cinzel",Georgia,serif;font-weight:700;font-size:30px;line-height:40px;white-space:nowrap;color:#fff;text-shadow:0 2px 4px rgba(0,0,0,.45)}
.hero-cta{left:381px;top:337px;width:403px;height:51px;background:rgba(95,95,95,.9);border:2px solid #bdbdbd;color:#fff;font-family:"Cinzel",Georgia,serif;font-size:24px;display:flex;align-items:center;justify-content:center;white-space:nowrap}
.hero-arrow{top:170px;width:20px;height:30px}

/* buttons */
.pill{position:absolute;height:30px;display:flex;align-items:center}
.pill span{background:var(--button);border:1px solid #8e8f91;height:26px;line-height:24px;padding:0 26px 0 10px;font-size:12px;font-weight:700;color:var(--ink);border-radius:3px 0 0 3px;white-space:nowrap}
.pill svg{width:32px;height:32px;margin-left:-14px}

/* welcome */
.welcome{top:577px;height:453px;background:var(--mist)}
.welcome h1{left:69px;top:60px;font-family:"Cinzel",Georgia,serif;font-weight:400;font-size:28px;color:var(--ink);white-space:nowrap}
.lead{left:69px;top:110px;width:680px;font-size:15px;line-height:24px;color:#222}
.body-copy{left:69px;top:176px;width:680px;font-size:13.4px;line-height:22px;color:#333}
.evaluation{left:797px;top:62px;width:330px;height:325px;border:2px solid #3a3c42;background:var(--mist)}
.evaluation h3{position:absolute;left:18px;top:20px;font-family:"Cinzel",Georgia,serif;font-weight:400;font-size:23px;color:var(--ink);white-space:nowrap}
.field{position:absolute;left:18px;width:292px;background:#fff;border:1px solid var(--line);font-size:12px;color:#444;padding:10px 10px}

/* practice */
.practice{top:1030px;height:423px;background:var(--paper)}
.area{position:absolute;top:123px;width:260px;text-align:center}
.area .icon{width:101px;height:101px;margin:0 auto;border:2px solid var(--ink);display:flex;align-items:center;justify-content:center;background:#fff}
.area .icon.active{background:var(--ink)}
.area .icon svg{width:56px;height:56px}
.area h3{font-family:"Cinzel",Georgia,serif;font-weight:400;font-size:19px;color:var(--ink);margin-top:22px;white-space:nowrap}
.area p{font-size:13px;line-height:18px;color:#333;margin:8px auto 0;width:200px}
.area .more{font-size:14px;margin-top:10px}
.side-arrow{position:absolute;width:18px;height:56px}

/* case studies */
.cases{top:1453px;height:527px;background:var(--mist)}
.case{position:absolute;top:123px;width:310px}
.case .frame{height:163px;border:1px solid #c4c4c4;background:#fff;padding:7px;position:relative}
.case .photo{width:100%;height:100%}
.date{position:absolute;left:10px;top:10px;width:46px;text-align:center}
.date b{display:block;background:var(--ink);color:#fff;font-size:17px;height:24px;line-height:24px}
.date i{display:block;background:#fff;color:var(--ink);font-style:normal;font-size:15px;height:22px;line-height:22px}
.case h4{font-size:13.4px;font-weight:700;color:#111;margin-top:20px;white-space:nowrap}
.case p{font-size:12.6px;line-height:19px;color:#333;margin-top:10px}
.case .read{font-size:12.6px;margin-top:10px;color:#222}

/* testimonials */
.testimonials{top:1980px;height:302px;background:var(--paper)}
.portrait{left:134px;top:119px;width:117px;height:117px}
.quote{left:318px;top:124px;width:760px;font-size:13.4px;line-height:21.5px;font-style:italic;color:#222}
.quote-mark{font-family:Georgia,serif;font-size:64px;color:#e1e1e1;line-height:1}
.author{left:308px;top:224px;font-family:"Cinzel",Georgia,serif;font-size:17px;color:var(--ink);white-space:nowrap}

/* cta band */
.cta-band{top:2282px;height:129px;background:var(--steel)}
.cta-band p{position:absolute;left:116px;top:28px;font-family:"Cinzel",Georgia,serif;font-size:28.5px;line-height:38px;color:#fff;letter-spacing:.5px;white-space:nowrap}
.cta-button{left:844px;top:40px;width:225px;height:48px;background:var(--ink);border:2px solid #d9d9d9;color:#fff;font-weight:700;font-size:23px;display:flex;align-items:center;justify-content:center}

/* footer */
.site-footer{top:2411px;height:267px;background:var(--dark);color:#fff}
.site-footer h5{position:absolute;top:42px;font-family:"Cinzel",Georgia,serif;font-weight:400;font-size:17px;color:#fff;padding-bottom:8px;border-bottom:1px solid #4c4e55;white-space:nowrap}
.quick-links{left:67px;top:88px;list-style:none;font-size:12.2px;line-height:24.6px}
.quick-links li::before{content:"";display:inline-block;width:4px;height:4px;background:#fff;border-radius:50%;margin:0 8px 3px 0}
.map{left:301px;top:85px;width:260px;height:124px;background:linear-gradient(135deg,#e4e2dc,#cfd7d0 50%,#e8e6e0);border:2px solid #fff}
.address{left:590px;top:88px;font-size:12.2px;line-height:19px;white-space:nowrap}
.address .row{display:flex;gap:12px;margin-bottom:8px}
.address svg{width:14px;height:14px;flex:none;margin-top:2px}
.footer-brand{left:866px;top:98px;width:300px;text-align:center;font-family:"Cinzel",Georgia,serif;font-size:15px;font-weight:600;color:#fff;white-space:nowrap;padding-bottom:6px;border-bottom:1px solid #fff}
.social{left:922px;top:150px;display:flex;gap:16px}
.social span{width:30px;height:30px;border-radius:50%;border:2px solid #fff;display:block}
.divider{top:42px;width:1px;height:180px;background:#4c4e55}

.copyright{top:2678px;height:45px;background:var(--steel);font-size:12.4px;color:#222}
.copyright .left{left:69px;top:14px;white-space:nowrap}
.copyright .right{left:827px;top:14px;white-space:nowrap}
</style>
</head>
<body>

<header class="site-header">
  <div class="abs brand">Calleja &amp; Ferro Advocates</div>
  <div class="abs contact-line" style="top:22px">
    <svg viewBox="0 0 26 26"><rect x="1" y="1" width="24" height="24" rx="5" fill="#2b2d33"/><rect x="9" y="5" width="8" height="16" rx="1.5" fill="none" stroke="#fff" stroke-width="1.8"/><circle cx="13" cy="18" r="1" fill="#fff"/></svg>
    555-014-2290
  </div>
  <div class="abs contact-line" style="top:57px">
    <svg viewBox="0 0 26 26"><rect x="1" y="1" width="24" height="24" rx="5" fill="#2b2d33"/><rect x="6" y="8" width="14" height="10" fill="none" stroke="#fff" stroke-width="1.6"/><path d="M6 8l7 6 7-6" fill="none" stroke="#fff" stroke-width="1.6"/></svg>
    info@callejaferro.example
  </div>
</header>

<nav class="main-nav">
  <ul>
    <li class="active" style="width:91px">Home</li>
    <li style="width:163px">About Malta</li>
    <li style="width:180px">Practice Areas</li>
    <li style="width:127px">Our Firm</li>
    <li style="width:145px">Our Values</li>
    <li style="width:203px">What Others Say</li>
    <li style="width:151px">Contact Us</li>
  </ul>
</nav>

<section class="hero">
  <div class="hero-photo" role="img" aria-label="Photograph of the Valletta skyline with a domed church at sunset"></div>
  <svg class="abs hero-arrow" style="left:20px" viewBox="0 0 20 30"><path d="M14 4L4 15l10 11" fill="none" stroke="#fff" stroke-width="3"/></svg>
  <svg class="abs hero-arrow" style="right:20px" viewBox="0 0 20 30"><path d="M6 4l10 11-10 11" fill="none" stroke="#fff" stroke-width="3"/></svg>
  <div class="abs hero-title">Realize Your Constitutional Right For Qualified Legal Help</div>
  <div class="abs hero-cta">Get A Free Consultation</div>
</section>

<section class="welcome">
  <h1 class="abs">Welcome To Calleja &amp; Ferro Advocates</h1>
  <p class="abs lead">Lorem ipsum dolor sit amet, consectetur adipiscing elit, sed diam nonummy nibh euismod tincidunt ut laoreet dolore magna aliquam erat volutpat.</p>
  <p class="abs body-copy">Lorem ipsum dolor sit amet, consectetur adipiscing elit. Sed vitae magna tellus. Aenean ante nunc, semper nec cursus non, rutrum ac eros. Vestibulum mattis justo ac dui bibendum consequat a ac ipsum. Praesent a arcu venenatis, auctor velit eu, suscipit libero. Quisque convallis, leo ac pharetra sagittis, ipsum arcu auctor urna, sit amet cursus risus augue in eros. Duis lacinia nisi vitae leo commodo, non finibus magna maximus. Sed posuere, neque eget bibendum pulvinar, ligula erat suscipit dolor, ut maximus arcu mi et tortor. Quisque imperdiet turpis et ligula mollis ultricies. Mauris lacinia rhoncus odio, at rutrum diam mollis eu. Quisque ut ipsum faucibus, tristique dui vitae, posuere orci.</p>
  <div class="pill" style="left:69px;top:358px"><span>READ MORE</span><svg viewBox="0 0 32 32"><circle cx="16" cy="16" r="15" fill="#2b2d33"/><path d="M13 10l6 6-6 6" fill="none" stroke="#fff" stroke-width="2.2"/></svg></div>

  <div class="abs evaluation">
    <h3>Free Case Evaluation</h3>
    <div class="field" style="top:80px;height:40px">Name</div>
    <div class="field" style="top:129px;height:40px">Email</div>
    <div class="field" style="top:180px;height:74px">Message</div>
    <div class="pill" style="left:18px;top:268px"><span style="font-size:13px;padding-right:30px">SUBMIT</span><svg viewBox="0 0 32 32" style="width:38px;height:38px"><circle cx="16" cy="16" r="15" fill="#2b2d33"/><path d="M13 10l6 6-6 6" fill="none" stroke="#fff" stroke-width="2.2"/></svg></div>
  </div>
</section>

<section class="practice">
  <h2 class="section-title" style="top:56px">Our Practice Areas</h2>
  <svg class="side-arrow" style="left:30px;top:213px" viewBox="0 0 18 56"><path d="M15 2L3 28l12 26" fill="none" stroke="#555" stroke-width="1.6"/></svg>
  <svg class="side-arrow" style="right:30px;top:213px" viewBox="0 0 18 56"><path d="M3 2l12 26-12 26" fill="none" stroke="#555" stroke-width="1.6"/></svg>

  <div class="area" style="left:70px">
    <div class="icon"><svg viewBox="0 0 56 56"><circle cx="18" cy="33" r="9" fill="none" stroke="#2b2d33" stroke-width="4"/><circle cx="38" cy="33" r="9" fill="none" stroke="#2b2d33" stroke-width="4"/><path d="M18 24l4-8h12l4 8" fill="none" stroke="#2b2d33" stroke-width="4"/></svg></div>
    <h3>Crimimal</h3>
    <p>Lorem ipsum dolor sit amet, consectetuer Lorem dolor sit amet, consectetuer</p>
    <div class="more">[+]</div>
  </div>
  <div class="area" style="left:329px">
    <div class="icon active"><svg viewBox="0 0 56 56"><rect x="14" y="8" width="28" height="40" rx="3" fill="#fff"/><circle cx="28" cy="24" r="7" fill="none" stroke="#2b2d33" stroke-width="2"/><path d="M21 24h14M28 17v14" stroke="#2b2d33" stroke-width="1.5"/><rect x="21" y="38" width="14" height="2.5" fill="#2b2d33"/></svg></div>
    <h3>Citizenship &amp; Residence</h3>
    <p>Lorem ipsum dolor sit amet, consectetuer Lorem dolor sit amet, consectetuer</p>
    <div class="more">[+]</div>
  </div>
  <div class="area" style="left:598px">
    <div class="icon"><svg viewBox="0 0 56 56"><circle cx="28" cy="15" r="7" fill="#2b2d33"/><rect x="14" y="24" width="28" height="18" rx="2" fill="#2b2d33"/><path d="M18 30h20M18 35h14" stroke="#fff" stroke-width="2"/><path d="M6 27h6M44 27h6M6 39h6M44 39h6" stroke="#2b2d33" stroke-width="2"/></svg></div>
    <h3>Criminal Defence</h3>
    <p>Lorem ipsum dolor sit amet, consectetuer Lorem dolor sit amet, consectetuer</p>
    <div class="more">[+]</div>
  </div>
  <div class="area" style="left:872px">
    <div class="icon"><svg viewBox="0 0 56 56"><rect x="22" y="6" width="14" height="20" rx="2" transform="rotate(45 29 16)" fill="#2b2d33"/><path d="M30 22l12 12" stroke="#2b2d33" stroke-width="5" stroke-linecap="round"/><rect x="8" y="42" width="26" height="6" fill="#2b2d33"/></svg></div>
    <h3>Civil Litigation</h3>
    <p>Lorem ipsum dolor sit amet, consectetuer Lorem dolor sit amet, consectetuer</p>
    <div class="more">[+]</div>
  </div>
</section>

<section class="cases">
  <h2 class="section-title" style="top:56px">Case Studies</h2>
  <article class="case" style="left:69px">
    <div class="frame"><div class="photo" role="img" aria-label="Photograph of rows of leather-bound law books" style="background:linear-gradient(90deg,#5a3a22,#a47a3e,#6b4727,#b08a4a,#4e3320)"></div>
      <div class="date"><b>06</b><i>Jun</i></div></div>
    <h4>Lorem Ipsum Dolor Sit Amet  Consectetur</h4>
    <p>Lorem ipsum dolor sit amet, consectetur adipiscing elit. Sed vitae magna tellus. Aenean ante nunc, semper nec cursus non, rutrum ac eros.</p>
    <div class="read">Read More ››</div>
  </article>
  <article class="case" style="left:445px">
    <div class="frame"><div class="photo" role="img" aria-label="Photograph of a handcuffed defendant standing in a courtroom" style="background:linear-gradient(135deg,#3b2418,#6e4632 50%,#2a2a2e)"></div>
      <div class="date"><b>06</b><i>Jun</i></div></div>
    <h4>Lorem Ipsum Dolor Sit Amet  Consectetur</h4>
    <p>Lorem ipsum dolor sit amet, consectetur adipiscing elit. Sed vitae magna tellus. Aenean ante nunc, semper nec cursus non, rutrum ac eros.</p>
    <div class="read">Read More ››</div>
  </article>
  <article class="case" style="left:819px">
    <div class="frame"><div class="photo" role="img" aria-label="Photograph of hands signing a legal document" style="background:linear-gradient(135deg,#4a4a4e,#dcdcdc 45%,#f4f4f4 70%,#8a8a8e)"></div>
      <div class="date"><b>07</b><i>Jun</i></div></div>
    <h4>Lorem Ipsum Dolor Sit Amet  Consectetur</h4>
    <p>Lorem ipsum dolor sit amet, consectetur adipiscing elit. Sed vitae magna tellus. Aenean ante nunc, semper nec cursus non, rutrum ac eros.</p>
    <div class="read">Read More ››</div>
  </article>
  <div class="pill" style="left:537px;top:451px"><span style="padding:0 30px 0 22px">VIEW ALL</span><svg viewBox="0 0 32 32"><circle cx="16" cy="16" r="15" fill="#2b2d33"/><path d="M13 10l6 6-6 6" fill="none" stroke="#fff" stroke-width="2.2"/></svg></div>
</section>

<section class="testimonials">
  <h2 class="section-title" style="top:58px">Client Testimonials</h2>
  <svg class="side-arrow" style="left:30px;top:143px" viewBox="0 0 18 56"><path d="M15 2L3 28l12 26" fill="none" stroke="#555" stroke-width="1.6"/></svg>
  <svg class="side-arrow" style="right:30px;top:143px" viewBox="0 0 18 56"><path d="M3 2l12 26-12 26" fill="none" stroke="#555" stroke-width="1.6"/></svg>
  <div class="abs portrait" role="img" aria-label="Portrait photograph of the client" style="background:linear-gradient(180deg,#e4e6ea,#c9ccd2 55%,#2f3440)"></div>
  <div class="abs quote-mark" style="left:306px;top:100px">“</div>
  <p class="abs quote">Lorem ipsum dolor sit amet, consectetuer adipiscing elit, sed diam nonummy nibh euismod tincidunt ut laoreet dolore magna aliquam erat volutpat. Ut wisi enim ad minim veniam, quis nostrud exerci iriure dolor in Lorem ipsum dolor sit amet, consectetuer adipiscing elit, sed diam nonummy nibh euismod tincidunt ut laoreet dolore magna aliquam erat volutpat. Ut wisi enim ad minim veniam, quis nostrud exerci iriure dolo.</p>
  <div class="abs quote-mark" style="left:538px;top:176px">”</div>
  <div class="abs author">- Daniel Rowe</div>
</section>

<section class="cta-band">
  <p>For Any Legal Problem, We Can Help You<br>Anytime take An Appointment Now</p>
  <div class="abs cta-button">CONTACT US</div>
</section>

<footer class="site-footer">
  <h5 style="left:67px;width:140px">Quick Links</h5>
  <ul class="abs quick-links">
    <li>Home</li><li>About Malta</li><li>Practice Areas</li><li>Our Firm</li><li>Our Values</li><li>What Others Say</li><li>Contact Us</li>
  </ul>
  <div class="abs divider" style="left:262px"></div>
  <h5 style="left:301px;width:490px">Contact Details</h5>
  <div class="abs map" role="img" aria-label="Street map showing the office location"></div>
  <div class="abs address">
    <div class="row"><svg viewBox="0 0 14 14"><path d="M7 1a4 4 0 0 0-4 4c0 3 4 8 4 8s4-5 4-8a4 4 0 0 0-4-4z" fill="#fff"/><circle cx="7" cy="5" r="1.5" fill="#2d2f35"/></svg><div><b>Calleja &amp; Ferro Advocates</b><br>12/4, Harbour Lane, Valletta<br>90, Olive Street, Mosta</div></div>
    <div class="row"><svg viewBox="0 0 14 14"><path d="M3 1l3 3-1.5 2c1 2 2 3 3.5 3.5L10 8l3 3-2 2C6 12 2 8 1 3z" fill="#fff"/></svg><div>555-014-229</div></div>
    <div class="row"><svg viewBox="0 0 14 14"><rect x="3" y="1" width="8" height="4" fill="#fff"/><rect x="1" y="5" width="12" height="6" fill="#fff"/><rect x="3" y="9" width="8" height="4" fill="#fff" stroke="#2d2f35"/></svg><div>555-014-229</div></div>
    <div class="row"><svg viewBox="0 0 14 14"><rect x="1" y="3" width="12" height="8" fill="#fff"/><path d="M1 3l6 5 6-5" fill="none" stroke="#2d2f35"/></svg><div>info@callejaferro.example</div></div>
  </div>
  <div class="abs divider" style="left:840px"></div>
  <div class="abs footer-brand">Calleja &amp; Ferro Advocates</div>
  <div class="abs social" aria-label="Social media links">
    <span style="background:#3b5998"></span><span style="background:#0e76a8"></span><span style="background:#1da1f2"></span><span style="background:#dd4b39"></span>
  </div>
</footer>

<section class="copyright">
  <div class="abs left">Copyright © 2016 <b>Calleja &amp; Ferro Advocates</b>. All Rights Reserved.</div>
  <div class="abs right">Terms &amp; Conditions &nbsp;|&nbsp; Privacy Policy &nbsp;|&nbsp; Disclaimer</div>
</section>

</body>
</html>
```